Existing Website Requiring new Pages

I have an existing word press website that was built using elementor.
Website: www.tallowcrestcare.com.au
I require the Vacancies page (https://www.tallowcrestcare.com.au/vacancies/) to be modified to display our new properties along with minor tweaks to how the information is presented.
The vacancies to be displayed are the exactly the same as those that are located on the homepage of QMR website (https://qmr.org.au/)
The new pages that link off the Vacancies tab will require custom design.
There are roughly 8 pages/properties to be incorporated. i wish for the design to be very similar to that displayed in the following link; https://www.polunda.com.au/vacancies/merrylands
Along with this the back end has not been updated for the last 3 years so it also requires some maintenance.
Website is in the disability industry and the custom pages will display information relative to Property Vacancies.
I have attached a ZIP file with some design guides, the information for each of the properties (which will need to be modified to show our business name Tallowcrest Care) and the example of how it is to look based off the Polunda website.
If you guys have any suggestions or ideas on how to make this more presentable or possible i'm open to your ideas.
Target Market(s)
People looking for SDA properties custom built for people with a disability
Industry/Entity Type
Disability
Coding
Coded - Design and coding required
Number of Pages Required
5+ page

```html
<!DOCTYPE html>
<html lang="en">
<head>
<meta charset="utf-8">
<meta name="format-detection" content="telephone=no">
<title>Vacancies – Tallowcrest Care</title>
<link rel="stylesheet" href="https://fonts.googleapis.com/css2?family=Oswald:wght@500;600&family=Montserrat:wght@400;600;700&display=swap">
<style>
:root{
  --ink:#333333;
  --muted:#8a8a8a;
  --accent:#f07b54;
  --pink:#e0408f;
  --teal:#1bc6c0;
  --blue:#1e88c7;
  --purple:#6b2a7e;
  --dark:#222222;
  --footer-bg:#f7f7f8;
  --bar-bg:#1c1c1c;
  --yellow:#ffc72c;
  --rule:#e3e3e3;
  --white:#ffffff;
}
*{box-sizing:border-box;margin:0;padding:0}
html,body{width:837px;height:1200px;overflow:hidden;background:var(--white)}
body{font-family:'Montserrat',sans-serif;color:var(--ink);position:relative}
.page{position:relative;width:837px;height:1200px;overflow:hidden}

/* header */
.site-header{position:absolute;top:0;left:0;width:837px;height:85px;background:var(--white)}
.brand{position:absolute;left:87px;top:30px;display:flex;align-items:center;gap:6px}
.brand-dot{width:12px;height:12px;border-radius:50%;background:var(--pink)}
.brand-name{font-family:'Oswald',sans-serif;font-weight:500;font-size:19px;color:var(--ink);letter-spacing:.5px}
.main-nav{position:absolute;top:37px;right:78px;display:flex;gap:16px}
.main-nav a{font-size:7.5px;font-weight:700;letter-spacing:.6px;color:var(--ink);text-decoration:none;text-transform:uppercase}
.main-nav a.current{color:var(--accent)}

/* hero */
.hero{position:absolute;top:85px;left:0;width:837px;height:385px}
.hero-photo{position:absolute;inset:0;background:linear-gradient(100deg,#8a7468 0%,#6e6561 35%,#5d6a58 65%,#b9aea3 100%)}
.hero-art{position:absolute;left:25px;top:45px;width:340px;height:330px;background:radial-gradient(ellipse at 45% 40%,#f04ca5 0%,#d063e3 40%,rgba(220,90,200,0) 70%)}
.hero-title{position:absolute;left:78px;top:135px;font-family:'Oswald',sans-serif;font-weight:600;font-size:56px;color:var(--white);letter-spacing:.5px}
.hero-edge{position:absolute;left:0;bottom:-1px;width:837px;height:16px;display:block}

/* vacancies grid */
.vacancies{position:absolute;top:543px;left:78px;width:681px;display:grid;grid-template-columns:repeat(4,159px);column-gap:15px;row-gap:49px}
.property-card{position:relative;width:159px;height:145px}
.property-photo{width:159px;height:145px;border-radius:9px}
.tone-a{background:linear-gradient(180deg,#dcdfe4 0%,#9c9790 60%,#6c8a4c 100%)}
.tone-b{background:linear-gradient(180deg,#a9cce9 0%,#b06e55 45%,#cf8e73 100%)}
.tone-c{background:linear-gradient(180deg,#8ec1ea 0%,#e8dcbd 55%,#4f7a3c 100%)}
.tone-d{background:linear-gradient(180deg,#c9ddee 0%,#e6d4b8 50%,#7d9d5a 100%)}
.tone-e{background:linear-gradient(180deg,#7fb6e8 0%,#d8c7ae 55%,#5f9a3a 100%)}
.tone-f{background:linear-gradient(180deg,#86b9eb 0%,#c76b44 45%,#9ab768 100%)}
.tone-g{background:linear-gradient(180deg,#a5c8e6 0%,#e9e6ea 45%,#8a6a44 100%)}
.tone-h{background:linear-gradient(180deg,#c8dbea 0%,#7b8594 50%,#4f8a3a 100%)}
.property-label{position:absolute;left:14px;top:119px;width:131px;height:44px;background:var(--white);border-radius:6px 6px 0 0;text-align:center;padding-top:6px}
.property-name{font-family:'Oswald',sans-serif;font-weight:500;font-size:16px;line-height:1;color:var(--ink)}
.property-type{font-size:9.5px;margin-top:5px;color:var(--ink)}
.property-type span{color:var(--ink)}

/* footer */
.site-footer{position:absolute;top:955px;left:0;width:837px;height:198px;background:var(--footer-bg)}
.footer-brand{position:absolute;left:78px;top:60px;display:flex;align-items:center;gap:6px}
.footer-brand .brand-name{font-size:21px}
.contact-list{position:absolute;left:76px;top:139px;list-style:none}
.contact-list li{display:flex;align-items:center;gap:6px;font-size:8.5px;color:var(--muted);height:15px}
.contact-list svg{width:10px;height:10px}
.social-list{position:absolute;left:360px;top:37px;display:flex;flex-direction:column;gap:6px}
.social-list span{width:22px;height:22px;border-radius:50%;display:flex;align-items:center;justify-content:center}
.social-list span::after{content:"";width:8px;height:8px;border-radius:50%;background:var(--white)}
.social-list .c1{background:var(--purple)}
.social-list .c2,.social-list .c4{background:var(--blue)}
.social-list .c3{background:var(--dark)}
.footer-col{position:absolute;top:36px;width:157px}
.footer-col.accom{left:423px}
.footer-col.services{left:597px}
.footer-col h3{font-size:9.5px;font-weight:600;letter-spacing:.5px;color:var(--ink);border-left:2px solid var(--blue);padding-left:9px;line-height:10px;margin-bottom:10px}
.footer-col ul{list-style:none;border-top:1px solid var(--rule)}
.footer-col li{font-size:8.5px;color:var(--muted);line-height:15px;padding:5px 0;border-bottom:1px solid var(--rule)}

.copyright-bar{position:absolute;top:1153px;left:0;width:837px;height:47px;background:var(--bar-bg);color:var(--white);font-size:8.5px;text-align:center;line-height:47px}
.back-to-top{position:absolute;right:38px;top:1162px;width:31px;height:30px;background:var(--yellow);border-radius:2px;display:flex;align-items:center;justify-content:center}
</style>
</head>
<body>
<div class="page">

  <header class="site-header">
    <div class="brand"><span class="brand-dot"></span><span class="brand-name">TALLOWCREST CARE</span></div>
    <nav class="main-nav">
      <a href="#">Home</a>
      <a href="#">About Us</a>
      <a href="#" class="current">What We Do ⌄</a>
      <a href="#">Referrals</a>
      <a href="#">Feedback</a>
      <a href="#">Contact Us</a>
    </nav>
  </header>

  <section class="hero">
    <div class="hero-photo" role="img" aria-label="Photo of a young woman with a prosthetic arm working at a laptop in an office"></div>
    <div class="hero-art" role="img" aria-label="Colourful painted tree with a swing"></div>
    <h1 class="hero-title">Vacancies</h1>
    <svg class="hero-edge" viewBox="0 0 837 16" preserveAspectRatio="none" aria-hidden="true">
      <defs>
        <pattern id="grass" x="0" y="0" width="14" height="16" patternUnits="userSpaceOnUse">
          <path d="M0 16 L1 8 L2.5 12 L4 3 L5.5 11 L7 6 L8.5 12 L10 1 L11.5 10 L13 5 L14 16 Z" fill="#ffffff"/>
        </pattern>
      </defs>
      <rect x="0" y="0" width="837" height="16" fill="url(#grass)"/>
      <rect x="0" y="12" width="837" height="4" fill="#ffffff"/>
    </svg>
  </section>

  <main class="vacancies">
    <article class="property-card"><div class="property-photo tone-a" role="img" aria-label="Penrith house exterior"></div><div class="property-label"><h2 class="property-name">Penrith</h2><p class="property-type"><span>4 Bedroom SIL Home</span></p></div></article>
    <article class="property-card"><div class="property-photo tone-b" role="img" aria-label="Mount Druitt house exterior"></div><div class="property-label"><h2 class="property-name">Mount Druitt</h2><p class="property-type"><span>4 Bedroom SIL Home</span></p></div></article>
    <article class="property-card"><div class="property-photo tone-c" role="img" aria-label="Casula house exterior"></div><div class="property-label"><h2 class="property-name">Casula</h2><p class="property-type"><span>4 Bedroom SIL Home</span></p></div></article>
    <article class="property-card"><div class="property-photo tone-d" role="img" aria-label="Eastwood house exterior"></div><div class="property-label"><h2 class="property-name">Eastwood</h2><p class="property-type"><span>4 Bedroom SIL Home</span></p></div></article>
    <article class="property-card"><div class="property-photo tone-e" role="img" aria-label="Baulkham Hills house exterior"></div><div class="property-label"><h2 class="property-name">Baulkham Hills</h2><p class="property-type"><span>4 Bedroom SIL Home</span></p></div></article>
    <article class="property-card"><div class="property-photo tone-f" role="img" aria-label="Merrylands house exterior"></div><div class="property-label"><h2 class="property-name">Merrylands</h2><p class="property-type"><span>4 Bedroom SIL Home</span></p></div></article>
    <article class="property-card"><div class="property-photo tone-g" role="img" aria-label="Burwood modern house exterior"></div><div class="property-label"><h2 class="property-name">Burwood</h2><p class="property-type"><span>4 Bedroom SIL Home</span></p></div></article>
    <article class="property-card"><div class="property-photo tone-h" role="img" aria-label="Surry Hills house exterior"></div><div class="property-label"><h2 class="property-name">Surry Hills</h2><p class="property-type"><span>4 Bedroom SIL Home</span></p></div></article>
  </main>

  <footer class="site-footer">
    <div class="footer-brand"><span class="brand-dot"></span><span class="brand-name">TALLOWCREST CARE</span></div>
    <ul class="contact-list">
      <li><svg viewBox="0 0 10 10"><rect x="0.5" y="1.5" width="9" height="7" rx="1" fill="none" stroke="#e0408f"/><path d="M0.5 2 L5 5.5 L9.5 2" fill="none" stroke="#e0408f"/></svg>Email: info@tallowcrestcare.com.au</li>
      <li><svg viewBox="0 0 10 10"><path d="M2 0.5 L4 2.5 L3 4 Q4.5 6 6 7 L7.5 6 L9.5 8 L8 9.5 Q3 9 0.5 2 Z" fill="#e0408f"/></svg>Phone: +61 0400 318 642</li>
      <li><svg viewBox="0 0 10 10"><circle cx="5" cy="5" r="4.3" fill="none" stroke="#e0408f"/><path d="M5 2.5 V5 L6.8 6.2" fill="none" stroke="#e0408f"/></svg>Operating Hours: 9AM To 5PM Monday - Friday</li>
    </ul>
    <div class="social-list" aria-label="Partner and social links"><span class="c1"></span><span class="c2"></span><span class="c3"></span><span class="c4"></span></div>
    <div class="footer-col accom">
      <h3>ACCOMMODATION</h3>
      <ul>
        <li>Supported Independent Living (SIL)</li>
        <li>Specialist Disability Accommodation (SDA)</li>
        <li>Short term Accommodation (Respite)</li>
        <li>Vacancies</li>
      </ul>
    </div>
    <div class="footer-col services">
      <h3>WHAT WE DO</h3>
      <ul>
        <li>In Home Care</li>
        <li>Social &amp; Community Services</li>
        <li>Therapeutic Supports</li>
        <li>Support Coordination</li>
        <li>Home Modifications</li>
      </ul>
    </div>
  </footer>

  <div class="copyright-bar">©Copyrights 2024 Tallowcrest Care &nbsp;|&nbsp; All Rights Reserved</div>
  <a class="back-to-top" href="#" aria-label="Back to top"><svg width="14" height="9" viewBox="0 0 14 9"><path d="M1 8 L7 2 L13 8" fill="none" stroke="#1c1c1c" stroke-width="2"/></svg></a>

</div>
</body>
</html>
```